New business card/stationary for a consulting company

I am looking for a clean and very professional looking business card for my consulting company as well as corresponding stationary. I am uploading our logo. I like simple and powerful for the feel. No graphics but I am open on everything else. Below is my contact information but would like the final to be in a version I can add my employees information into and print. Thank you.

Daniel Whitcombe
dan@ferncliffadvisory.com
2870 North 9th Avenue, Summit Floor, Elm Ridge, Illinois 60531
www.ferncliffadvisory.com

Industry/Entity Type

Consulting

Contact Information for Business Card

Daniel Whitcombe
dan@ferncliffadvisory.com
www.ferncliffadvisory.com

Font styles to use
Serif
Sans Serif

Requirements
Must have
• Our logo and the business card details.
Nice to have
• our website www.ferncliffadvisory.com

```html
<!DOCTYPE html>
<html lang="en">
<head>
<meta charset="utf-8">
<title>Ferncliff Advisory – Business Card</title>
<link href="https://fonts.googleapis.com/css2?family=Cinzel:wght@700&family=Questrial&family=Roboto:wght@400;700&display=swap" rel="stylesheet">
<style>
  :root {
    --navy: #020066;
    --paper: #f3f3f3;
    --silver: #d6d6d6;
    --white: #ffffff;
    --ink-grey: #555555;
    --backdrop: #e8e5e1;
  }
  * { margin: 0; padding: 0; box-sizing: border-box; }
  html, body { width: 1200px; height: 960px; overflow: hidden; }
  body { background: var(--backdrop); position: relative; font-family: "Roboto", Arial, sans-serif; }

  .card { position: absolute; width: 600px; height: 343px; box-shadow: 0 2px 6px rgba(0,0,0,0.35); overflow: hidden; }
  .card-front { left: 302px; top: 129px; background: var(--paper); }
  .card-back { left: 299px; top: 488px; background: var(--navy); }

  .front-band { position: absolute; left: 0; top: 0; width: 600px; height: 189px; background: var(--navy); }
  .front-rule { position: absolute; left: 0; top: 191px; width: 600px; height: 4px; background: var(--navy); }

  .brand-square { position: absolute; background: var(--silver); }
  .front-band .brand-square { left: 277px; top: 62px; width: 44px; height: 44px; }
  .brand-name { position: absolute; left: 0; width: 100%; text-align: center; color: var(--white); font-family: "Questrial", "Century Gothic", sans-serif; font-weight: 400; white-space: nowrap; }
  .front-band .brand-name { top: 125px; font-size: 26px; letter-spacing: 0.5px; }

  .person { position: absolute; right: 339px; top: 243px; text-align: right; }
  .person-name { font-family: "Cinzel", "Copperplate", serif; font-weight: 700; font-size: 20px; color: var(--navy); line-height: 24px; letter-spacing: 0.3px; }
  .person-email { font-size: 14px; color: var(--ink-grey); line-height: 18px; }

  .address { position: absolute; left: 290px; top: 240px; font-size: 14px; color: var(--ink-grey); line-height: 18.5px; }
  .address .site { font-weight: 700; }

  .card-back .brand-square { left: 272px; top: 104px; width: 56px; height: 56px; }
  .card-back .brand-name { top: 180px; font-size: 34px; letter-spacing: 1px; }
  .back-site { position: absolute; left: 0; top: 287px; width: 100%; text-align: center; color: var(--white); font-family: "Cinzel", "Copperplate", serif; font-weight: 700; font-size: 12px; letter-spacing: 3px; }
</style>
</head>
<body>
  <section class="card card-front">
    <div class="front-band">
      <div class="brand-square"></div>
      <div class="brand-name">FERNCLIFF ADVISORY</div>
    </div>
    <div class="front-rule"></div>
    <div class="person">
      <div class="person-name">Daniel Whitcombe</div>
      <div class="person-email">dan@ferncliffadvisory.com</div>
    </div>
    <div class="address">
      <div>2870 North 9th Avenue</div>
      <div>Summit Floor, Elm Ridge, Illinois 60531</div>
      <div class="site">FERNCLIFFADVISORY.COM</div>
    </div>
  </section>

  <section class="card card-back">
    <div class="brand-square"></div>
    <div class="brand-name">FERNCLIFF ADVISORY</div>
    <div class="back-site">WWW.FERNCLIFFADVISORY.COM</div>
  </section>
</body>
</html>
```